Vitamin B12 Liquid Drops Label

hi, i need a label designed for my vitamin b12 drops that i am going to be selling on shopzello. the label needs to quickly capture the attention of a buyer as he or she is scrolling through the thumbnail search results on shopzello.com my brand is called nralo. i already have an example brand logo i will be using, however, i need help designing the rest of the label. attached are some examples of labels i like for other supplements.some of these examples are pink. i do not want pink. please go for a blue/green color scheme. THE DESIGN MUST BE BOLD

Target Market(s)

adults ages 30 - 64

Font styles to use
Sans Serif

Colors
0455a3
cedeed
3176b5
85acd3
cfdeed
9bcb3b
abd037
cadf82
00a990

Requirements
Must have
• - bold design
• - somewhat gender-neutral color scheme because this will be used equally by men and women
• - B12 MUST be very prominent and visible on the label
Should not have
• - it should not be "crunchy" looking

```html
<!DOCTYPE html>
<html lang="en">
<head>
<meta charset="utf-8">
<title>nralo Vitamin B12 – Packaging</title>
<link rel="stylesheet" href="https://fonts.googleapis.com/css2?family=Ubuntu:wght@500;700&display=swap">
<style>
  :root {
    --backdrop: #cedeed;
    --green: #9bcb3b;
    --green-light: #cadf82;
    --blue: #0455a3;
    --blue-deep: #03427f;
    --teal: #00a990;
  }
  * { margin: 0; padding: 0; box-sizing: border-box; }
  html, body { width: 1200px; height: 800px; overflow: hidden; }
  body {
    background: var(--backdrop);
    font-family: "Ubuntu", sans-serif;
    position: relative;
  }
  .carton-face {
    position: absolute;
    left: 170px; top: 90px;
    width: 340px; height: 620px;
  }
  .carton-face svg { display: block; width: 100%; height: 100%; }
  .carton-text { font-family: "Ubuntu", sans-serif; font-weight: 700; }

  .drop-label {
    position: absolute;
    left: 620px; top: 190px;
    width: 380px; height: 440px;
    background: var(--blue);
    overflow: hidden;
  }
  .drop-label .label-art {
    position: absolute; inset: 0;
    width: 100%; height: 100%;
  }
  .label-strength {
    position: absolute;
    left: 18px; top: 40px;
    font-size: 120px; font-weight: 700;
    color: var(--blue);
    letter-spacing: -2px;
    line-height: 1;
  }
  .label-details {
    position: absolute;
    left: 20px; top: 250px;
    color: var(--green-light);
    font-weight: 700;
  }
  .label-dose { font-size: 30px; letter-spacing: 1px; }
  .label-form { font-size: 30px; letter-spacing: 5px; margin-top: 8px; }
  .label-form-sub { font-size: 15px; letter-spacing: 5px; margin-top: 2px; }
  .label-origin {
    position: absolute;
    left: 20px; bottom: 30px;
    color: var(--green-light);
    font-weight: 700;
    font-size: 20px;
    line-height: 1.2;
  }
  .label-origin span { display: block; letter-spacing: 14px; }
  .label-brand {
    position: absolute;
    right: 18px; bottom: 30px;
    color: var(--green-light);
    font-weight: 700;
    font-size: 44px;
    line-height: 1;
  }
</style>
</head>
<body>

  <div class="carton-face">
    <svg viewBox="0 0 340 620" aria-label="nralo Vitamin B12 carton front">
      <rect width="340" height="620" fill="var(--green)"/>
      <rect width="340" height="40" fill="var(--blue)"/>
      <polygon points="0,342 340,216 340,306 0,432" fill="var(--blue)"/>
      <polygon points="0,432 120,388 340,522 340,620 307,620 0,486" fill="var(--blue)"/>
      <text class="carton-text" x="0" y="0" font-size="76" fill="var(--blue)"
            transform="translate(22 322) rotate(-20.3)">nralo</text>
      <text class="carton-text" x="0" y="0" font-size="42" fill="var(--green-light)"
            transform="translate(24 398) rotate(-20.3)">VITAMIN B12</text>
    </svg>
  </div>

  <div class="drop-label">
    <svg class="label-art" viewBox="0 0 380 440" preserveAspectRatio="none" aria-hidden="true">
      <rect width="380" height="440" fill="var(--blue)"/>
      <polygon points="0,0 300,0 240,190 0,190" fill="var(--green)"/>
    </svg>
    <div class="label-strength">B12</div>
    <div class="label-details">
      <div class="label-dose">5000 MCG*</div>
      <div class="label-form">METHYL</div>
      <div class="label-form-sub">COBAMALIN</div>
    </div>
    <div class="label-origin">MADE IN<span>USA</span></div>
    <div class="label-brand">nralo</div>
  </div>

</body>
</html>
```